Recipe Card Design

I have a small kitchen store in Livingston Montana, and I would like to have recipe cards (4x6 postcard) designed with my logo, lines for recipe writing, all in black and white. My website is here: www.brambleforkcookware.com

Store

```html
<!DOCTYPE html>
<html lang="en">
<head>
<meta charset="utf-8">
<title>Recipe Card – Bramble Fork Cookware</title>
<link rel="stylesheet" href="https://fonts.googleapis.com/css2?family=Montserrat:wght@500;600;700&family=Pinyon+Script&display=swap">
<style>
  :root {
    --ink: #111111;
    --paper: #ffffff;
    --rule: #1a1a1a;
    --icon-tone: #1c1c1c;
  }
  * { box-sizing: border-box; margin: 0; padding: 0; }
  html, body { width: 1200px; height: 800px; overflow: hidden; background: var(--paper); }
  .card {
    position: relative;
    width: 1200px;
    height: 800px;
    background: var(--paper);
    color: var(--ink);
    font-family: "Montserrat", Arial, sans-serif;
  }
  .rules { position: absolute; inset: 0; width: 1200px; height: 800px; }
  .rules line { stroke: var(--rule); stroke-width: 1.6; }
  .heading-script {
    position: absolute;
    font-family: "Pinyon Script", cursive;
    font-weight: 400;
    line-height: 1;
    color: var(--ink);
  }
  .title-recipe { left: 58px; top: 2px; font-size: 132px; letter-spacing: -2px; }
  .title-for {
    position: absolute;
    left: 304px; top: 132px;
    font-size: 36px; font-weight: 700; letter-spacing: 0.5px; line-height: 1;
  }
  .title-icons {
    position: absolute; left: 60px; top: 140px; width: 122px; height: 24px;
    background: var(--icon-tone); border-radius: 4px;
  }
  .section-label { top: 198px; font-size: 44px; }
  .section-label.ingredients { left: 58px; }
  .section-label.instructions { left: 428px; }
  .info-box {
    position: absolute; left: 1032px; width: 132px; height: 118px;
    border: 1.2px solid var(--rule);
    padding: 6px 4px;
    font-size: 21px; font-weight: 600; line-height: 1.35; letter-spacing: 0;
  }
  .info-box.serves { top: 210px; }
  .info-box.cooking-time { top: 336px; }
  .info-box.oven-temp { top: 460px; }
  .store-mark {
    position: absolute; left: 1024px; top: 600px; width: 146px; height: 172px;
    display: flex; flex-direction: column; align-items: center; justify-content: center; gap: 14px;
    text-align: center;
  }
  .store-mark .square { width: 34px; height: 34px; background: var(--ink); }
  .store-mark .store-name { font-size: 17px; font-weight: 600; line-height: 1.3; letter-spacing: 0.5px; text-transform: uppercase; }
  .website {
    position: absolute; left: 430px; top: 760px;
    font-size: 17px; font-weight: 600; letter-spacing: 2.2px; line-height: 1;
  }
</style>
</head>
<body>
<main class="card">
  <svg class="rules" viewBox="0 0 1200 800" aria-hidden="true">
    <g class="title-rules">
      <line x1="430" y1="96" x2="1164" y2="96"/>
      <line x1="430" y1="130" x2="1164" y2="130"/>
      <line x1="430" y1="164" x2="1164" y2="164"/>
    </g>
    <g class="ingredient-rules">
      <line x1="58" y1="261" x2="378" y2="261"/><line x1="58" y1="295" x2="378" y2="295"/>
      <line x1="58" y1="329" x2="378" y2="329"/><line x1="58" y1="363" x2="378" y2="363"/>
      <line x1="58" y1="397" x2="378" y2="397"/><line x1="58" y1="431" x2="378" y2="431"/>
      <line x1="58" y1="465" x2="378" y2="465"/><line x1="58" y1="499" x2="378" y2="499"/>
      <line x1="58" y1="533" x2="378" y2="533"/><line x1="58" y1="567" x2="378" y2="567"/>
      <line x1="58" y1="601" x2="378" y2="601"/><line x1="58" y1="634" x2="378" y2="634"/>
      <line x1="58" y1="668" x2="378" y2="668"/><line x1="58" y1="702" x2="378" y2="702"/>
      <line x1="58" y1="736" x2="378" y2="736"/>
    </g>
    <g class="instruction-rules">
      <line x1="430" y1="261" x2="996" y2="261"/><line x1="430" y1="295" x2="996" y2="295"/>
      <line x1="430" y1="329" x2="996" y2="329"/><line x1="430" y1="363" x2="996" y2="363"/>
      <line x1="430" y1="397" x2="996" y2="397"/><line x1="430" y1="431" x2="996" y2="431"/>
      <line x1="430" y1="465" x2="996" y2="465"/><line x1="430" y1="499" x2="996" y2="499"/>
      <line x1="430" y1="533" x2="996" y2="533"/><line x1="430" y1="567" x2="996" y2="567"/>
      <line x1="430" y1="601" x2="996" y2="601"/><line x1="430" y1="634" x2="996" y2="634"/>
      <line x1="430" y1="668" x2="996" y2="668"/><line x1="430" y1="702" x2="996" y2="702"/>
      <line x1="430" y1="736" x2="996" y2="736"/>
    </g>
  </svg>

  <h1 class="heading-script title-recipe">Recipe</h1>
  <div class="title-icons" role="img" aria-label="Small row of kitchenware icons"></div>
  <span class="title-for">FOR</span>

  <h2 class="heading-script section-label ingredients">Ingredients</h2>
  <h2 class="heading-script section-label instructions">Instructions</h2>

  <div class="info-box serves">SERVES</div>
  <div class="info-box cooking-time">COOKING<br>TIME</div>
  <div class="info-box oven-temp">OVEN<br>TEMP.</div>

  <div class="store-mark">
    <span class="square"></span>
    <span class="store-name">Bramble Fork<br>Cookware</span>
  </div>

  <p class="website">www.brambleforkcookware.com</p>
</main>
</body>
</html>
```